Business Card Design Project

Business Card
We are rebranding with a new logo
Industry/Entity Type
Business
Contact Information for Business Card
Dennis Morvale +61 487215963 dennis@quorv.com.au P.O. Box 872 Fernlow QLD 4309
Requirements
Must have
- Logo

```html
<!DOCTYPE html>
<html lang="en">
<head>
<meta charset="UTF-8">
<title>Quorv International – Business Card</title>
<link rel="stylesheet" href="https://fonts.googleapis.com/css2?family=Josefin+Sans:wght@600;700&family=Patrick+Hand&family=Raleway:wght@300;400&display=swap">
<style>
  :root {
    --backdrop: #e9e9e7;
    --card: #ffffff;
    --ink: #1c1c1c;
    --ink-soft: #3a3a3a;
    --brand-blue: #1c86bd;
    --email-blue: #2f6f97;
    --rule: #4a4a4a;
    --accent-fade: rgba(120, 160, 205, 0.22);
    --accent-warm: rgba(240, 170, 110, 0.18);
  }
  * { margin: 0; padding: 0; box-sizing: border-box; }
  html, body {
    width: 1200px;
    height: 800px;
    overflow: hidden;
    background: var(--backdrop);
  }
  .canvas {
    position: relative;
    width: 1200px;
    height: 800px;
  }
  .business-card {
    position: absolute;
    left: 75px;
    top: 100px;
    width: 1050px;
    height: 600px;
    background: var(--card);
    box-shadow: 0 10px 30px rgba(0, 0, 0, 0.12);
    overflow: hidden;
  }
  .card-decoration {
    position: absolute;
    left: 40px;
    top: 250px;
    width: 300px;
    height: 300px;
  }
  .holder-name {
    position: absolute;
    left: 150px;
    top: 215px;
    font-family: "Josefin Sans", sans-serif;
    font-weight: 700;
    font-size: 22px;
    letter-spacing: 2px;
    text-transform: uppercase;
    color: var(--ink);
  }
  .holder-phone {
    position: absolute;
    left: 200px;
    top: 318px;
    font-family: "Patrick Hand", cursive;
    font-size: 46px;
    letter-spacing: 1px;
    color: var(--ink);
  }
  .holder-address {
    position: absolute;
    left: 208px;
    top: 385px;
    font-family: "Raleway", sans-serif;
    font-weight: 400;
    font-size: 15px;
    color: var(--ink-soft);
  }
  .brand-block {
    position: absolute;
    left: 585px;
    top: 120px;
    display: flex;
    align-items: center;
    gap: 14px;
  }
  .brand-mark {
    width: 22px;
    height: 22px;
    border-radius: 50%;
    background: var(--brand-blue);
  }
  .brand-name {
    font-family: "Josefin Sans", sans-serif;
    font-weight: 700;
    font-size: 30px;
    letter-spacing: 3px;
    text-transform: uppercase;
    color: var(--brand-blue);
    line-height: 1;
    padding-top: 4px;
  }
  .email-line {
    position: absolute;
    left: 545px;
    top: 345px;
    display: flex;
    align-items: center;
    gap: 18px;
  }
  .email-line .rule {
    width: 60px;
    height: 1px;
    background: var(--rule);
  }
  .holder-email {
    font-family: "Raleway", sans-serif;
    font-weight: 300;
    font-size: 19px;
    letter-spacing: 4px;
    color: var(--email-blue);
  }
</style>
</head>
<body>
  <main class="canvas">
    <section class="business-card">
      <svg class="card-decoration" viewBox="0 0 300 300" aria-hidden="true">
        <circle cx="150" cy="150" r="130" fill="var(--accent-fade)"/>
        <circle cx="150" cy="150" r="80" fill="var(--accent-warm)"/>
      </svg>

      <p class="holder-name">Dennis Morvale</p>
      <p class="holder-phone">+61 487215963</p>
      <p class="holder-address">P.O. Box 872 Fernlow QLD 4309</p>

      <div class="brand-block">
        <span class="brand-mark"></span>
        <span class="brand-name">Quorv International</span>
      </div>

      <div class="email-line">
        <span class="rule"></span>
        <span class="holder-email">dennis@quorv.com.au</span>
        <span class="rule"></span>
      </div>
    </section>
  </main>
</body>
</html>
```